Billboard design 8x3M RAVU (Spanish company)

We´re located in the south of Spain. We run a local telecom company.
We sell Fiber optic, and mobile phone lines mainly.
The billboard will have to be in Spanish, I would like the price to be something you spot on first sight when passing by in the car.
Our company color is blue, like in our logo which I will add. I will also add a example from what we currently have.
The new offer should be:
1000 megas + 100Gigas movil con llamadas ilimitadas. (meaning 1000Mb fiber optic speed and 100Gb data and unlimited calls for 1 mobile line)
Our details are: phone line 958 47 6620
Website: ra-vu.es

```html
<!DOCTYPE html>
<html lang="es">
<head>
<meta charset="utf-8">
<title>RAVU – Valla 8x3 Fibra + Móvil</title>
<link href="https://fonts.googleapis.com/css2?family=Montserrat:wght@600;700;800;900&display=swap" rel="stylesheet">
<style>
  :root {
    --navy: #0b1f6b;
    --navy-deep: #07154f;
    --blue: #1440b8;
    --blue-bright: #2f7cf0;
    --yellow: #ffd21a;
    --white: #ffffff;
    --stage: #e9edf3;
  }
  * { margin: 0; padding: 0; box-sizing: border-box; }
  html, body {
    width: 1200px; height: 1000px; overflow: hidden;
    background: var(--stage);
    font-family: "Montserrat", Arial, sans-serif;
  }
  .billboard {
    position: absolute; left: 0; top: 275px;
    width: 1200px; height: 450px;
    display: flex;
    background: var(--navy);
    overflow: hidden;
  }
  .brand-panel {
    width: 330px; height: 100%;
    background: var(--navy);
    padding: 70px 0 0 42px;
    color: var(--white);
  }
  .brand-name {
    font-size: 78px; font-weight: 800; line-height: 1;
    letter-spacing: 2px; color: var(--white);
  }
  .brand-services {
    margin-top: 10px; font-size: 17px; font-weight: 600; letter-spacing: .5px;
  }
  .brand-claim {
    margin-top: 36px; font-size: 24px; font-weight: 700; line-height: 1.25;
  }
  .divider {
    width: 250px; height: 3px; background: var(--yellow); margin: 26px 0 28px;
  }
  .contact {
    color: var(--yellow); font-weight: 800; font-size: 28px; line-height: 1.4;
  }
  .contact-phone { display: flex; align-items: center; gap: 10px; }
  .contact-phone svg { width: 16px; height: 28px; }
  .offer-panel {
    position: relative; flex: 1; height: 100%;
    background:
      radial-gradient(ellipse at 72% 45%, var(--blue-bright) 0%, var(--blue) 40%, var(--navy-deep) 85%);
  }
  .offer-text { position: absolute; left: 30px; top: 48px; }
  .speed, .data {
    color: var(--yellow); font-weight: 900; line-height: .95;
    font-size: 108px; letter-spacing: -2px;
  }
  .speed .unit, .data .unit { font-size: 40px; font-weight: 800; letter-spacing: 0; margin-left: 8px; }
  .calls {
    margin-top: 18px; color: var(--white); font-size: 17px; font-weight: 800; letter-spacing: .3px;
  }
  .price { margin-top: 4px; color: var(--white); font-weight: 900; display: flex; align-items: baseline; }
  .price .per { font-size: 22px; font-weight: 800; margin-right: 8px; }
  .price .amount { font-size: 104px; letter-spacing: -2px; line-height: 1; }
  .hero-art {
    position: absolute; left: 360px; top: 40px; width: 480px; height: 370px;
    border-radius: 24px;
    background: radial-gradient(ellipse at 45% 50%, rgba(255,255,255,.35) 0%, rgba(90,160,255,.25) 45%, rgba(255,210,26,0) 75%);
  }
</style>
</head>
<body>
  <main class="billboard">
    <section class="brand-panel">
      <div class="brand-name">RAVU</div>
      <div class="brand-services">Wifi | Fibra | Movil | Tv</div>
      <p class="brand-claim">TU FIBRA + MÓVIL<br>AL MEJOR PRECIO</p>
      <div class="divider"></div>
      <div class="contact">
        <div class="contact-phone">
          <svg viewBox="0 0 16 28" aria-hidden="true"><rect x="1.5" y="1.5" width="13" height="25" rx="3" fill="none" stroke="#ffd21a" stroke-width="2"/><line x1="6" y1="23" x2="10" y2="23" stroke="#ffd21a" stroke-width="2"/></svg>
          <span>958 47 66 20</span>
        </div>
        <div class="contact-web">www.ra-vu.es</div>
      </div>
    </section>
    <section class="offer-panel">
      <div class="offer-text">
        <div class="speed">1000<span class="unit">Mb</span></div>
        <div class="data">+100<span class="unit">Gb</span></div>
        <div class="calls">MOVIL CON LLAMADAS ILIMITADAS</div>
        <div class="price"><span class="per">por</span><span class="amount">18.45€</span></div>
      </div>
      <div class="hero-art" role="img" aria-label="Balón de fútbol con estela de luz azul y dorada junto a un móvil y un portátil que muestran 100 GB"></div>
    </section>
  </main>
</body>
</html>
```